Dietitian needs awesome business card

I need a contemporary design that's eye catching but professional.
My card is to given to doctors, specialists and patients alike.
I manage patients with chronic diseases
I have uploaded my logo and current business card, I would also like the other Certified Clinical Nutritionist logo incorporated into the design

Target Market(s)

Doctors, specialists and patients

Industry/Entity Type

Healthcare

Contact Information for Business Card

www.brightfieldnutrition.com.au
Ph: 0427 561 903
Fax: 6457 2183
email: marcus.k.diet@fernmail.com
Space on the back of the card with: Appointment date, Appointment time and appointment location

Font styles to use
Serif

Colors
fbee3e
876aae
ffc214

Requirements
Must have
• My Logo
• Certified Clinical Nutritionist Logo
• My 4 locations - Pinebrook Medical Centre, North Corrin Health, Hollis Medical, Ashcombe Doctors Surgery
Nice to have
• I like the colours in my current business card

```html
<!DOCTYPE html>
<html lang="en">
<head>
<meta charset="utf-8">
<title>Brightfield Nutrition &amp; Dietetics – Business Card</title>
<link rel="stylesheet" href="https://fonts.googleapis.com/css2?family=Libre+Baskerville:wght@700&family=Montserrat:wght@500;600&family=Questrial&display=swap">
<style>
  :root {
    --blue: #2f6fe0;
    --blue-deep: #2557c9;
    --green: #8fdc1f;
    --orange: #f26a22;
    --white: #ffffff;
    --page: #e9e9ec;
    --ink-faint: rgba(47, 111, 224, 0.08);
    --line: #7f9ee6;
  }
  * { box-sizing: border-box; margin: 0; padding: 0; }
  html, body { width: 1200px; height: 1200px; overflow: hidden; background: var(--page); }
  .canvas { position: relative; width: 1200px; height: 1200px; }

  .card {
    position: absolute; left: 100px; width: 1000px; height: 560px;
    background: var(--white); overflow: hidden;
    box-shadow: 0 6px 20px rgba(0,0,0,0.15);
  }

  /* Appointment side */
  .card--back { top: 40px; }
  .back__top-band { position: absolute; top: 0; left: 0; right: 0; height: 10px; background: var(--green); }
  .back__title {
    position: absolute; top: 30px; width: 100%; text-align: center;
    font-family: "Montserrat", sans-serif; font-weight: 600; font-size: 62px;
    letter-spacing: 6px; color: var(--blue);
  }
  .back__watermark { position: absolute; left: 30px; top: 180px; width: 940px; height: 260px; }
  .back__watermark-dot {
    position: absolute; left: 0; top: 20px; width: 230px; height: 230px;
    border-radius: 50%; background: var(--ink-faint);
  }
  .back__watermark-name {
    position: absolute; left: 290px; top: 40px;
    font-family: "Questrial", sans-serif; font-size: 120px; color: var(--ink-faint);
  }
  .field { position: absolute; left: 75px; right: 68px; display: flex; align-items: flex-end; }
  .field__label { font-family: "Questrial", sans-serif; font-size: 32px; color: var(--blue); margin-right: 16px; }
  .field__line { flex: 1; border-bottom: 1.5px solid var(--line); margin-bottom: 6px; }
  .field--date { top: 140px; }
  .field--time { top: 290px; }
  .field--location { top: 435px; }
  .back__green-band { position: absolute; left: 0; right: 0; bottom: 52px; height: 8px; background: var(--green); }
  .back__blue-band {
    position: absolute; left: 0; right: 0; bottom: 0; height: 52px; background: var(--blue);
    display: flex; align-items: center; justify-content: flex-end; padding-right: 32px;
    font-family: "Montserrat", sans-serif; font-weight: 500; font-size: 28px; color: var(--white);
  }

  /* Front side */
  .card--front { top: 620px; }
  .front__name {
    position: absolute; left: 40px; top: 30px;
    font-family: "Libre Baskerville", serif; font-weight: 700; font-size: 50px;
    letter-spacing: 14px; line-height: 1.55; color: var(--green);
  }
  .front__name span { display: block; }
  .front__name span:last-child { margin-left: -10px; }
  .brand { position: absolute; left: 570px; top: 22px; display: flex; align-items: center; }
  .brand__dot { width: 78px; height: 78px; border-radius: 50%; background: var(--blue); margin-right: 14px; }
  .brand__name { font-family: "Questrial", sans-serif; font-size: 40px; line-height: 1.05; color: var(--blue); }
  .brand__name small { display: block; font-size: 21px; }

  .front__contact {
    position: absolute; left: 0; top: 210px; width: 560px; height: 260px; background: var(--blue);
    padding: 26px 0 0 80px; color: var(--white);
  }
  .contact__item { margin-bottom: 14px; }
  .contact__label { font-family: "Libre Baskerville", serif; font-weight: 700; font-size: 19px; display: block; }
  .contact__value { font-family: "Montserrat", sans-serif; font-weight: 500; font-size: 22px; }

  .front__locations {
    position: absolute; left: 560px; top: 130px; width: 440px; height: 270px; background: var(--green);
    padding: 22px 0 0 60px; font-family: "Questrial", sans-serif;
  }
  .locations__heading {
    display: inline-block; font-size: 32px; color: var(--white); letter-spacing: 3px;
    border-bottom: 2px solid var(--white); margin: 0 0 14px 60px;
  }
  .locations__list { list-style: none; }
  .locations__list li { font-size: 25px; color: var(--blue-deep); margin-bottom: 12px; }

  .credential {
    position: absolute; left: 830px; top: 400px; width: 170px; height: 70px; background: var(--orange);
    display: flex; align-items: center; padding: 0 10px; gap: 8px;
  }
  .credential__text { font-family: "Montserrat", sans-serif; font-weight: 500; font-size: 13px; line-height: 1.15; color: var(--white); flex: 1; }
  .credential__badge { width: 48px; height: 48px; border-radius: 50%; background: var(--white); }

  .front__roles {
    position: absolute; left: 0; right: 0; top: 490px; text-align: center;
    font-family: "Montserrat", sans-serif; font-weight: 600; font-size: 34px;
    letter-spacing: 3px; color: var(--green);
  }
</style>
</head>
<body>
<main class="canvas">

  <section class="card card--back" aria-label="Appointment card">
    <div class="back__top-band"></div>
    <h1 class="back__title">APPOINTMENT</h1>
    <div class="back__watermark" aria-hidden="true">
      <div class="back__watermark-dot"></div>
      <div class="back__watermark-name">Brightfield</div>
    </div>
    <div class="field field--date"><span class="field__label">Date</span><span class="field__line"></span></div>
    <div class="field field--time"><span class="field__label">Time</span><span class="field__line"></span></div>
    <div class="field field--location"><span class="field__label">Location</span><span class="field__line"></span></div>
    <div class="back__green-band"></div>
    <div class="back__blue-band">www.brightfieldnutrition.com.au</div>
  </section>

  <section class="card card--front" aria-label="Business card">
    <h2 class="front__name"><span>Marcus</span><span>Kendrick</span></h2>

    <div class="brand">
      <div class="brand__dot"></div>
      <div class="brand__name">Brightfield<small>Nutrition &amp; Dietetics</small></div>
    </div>

    <div class="front__contact">
      <div class="contact__item"><span class="contact__label">Tel:</span><span class="contact__value">0427 561 903</span></div>
      <div class="contact__item"><span class="contact__label">Fax:</span><span class="contact__value">6457 2183</span></div>
      <div class="contact__item"><span class="contact__label">Email:</span><span class="contact__value">marcus.k.diet@fernmail.com</span></div>
    </div>

    <div class="front__locations">
      <div class="locations__heading">Located</div>
      <ul class="locations__list">
        <li>Pinebrook Medical Centre</li>
        <li>Ashcombe Doctors Surgery</li>
        <li>North Corrin Health</li>
        <li>Hollis Medical</li>
      </ul>
    </div>

    <div class="credential">
      <span class="credential__text">Certified Clinical Nutritionist</span>
      <span class="credential__badge" aria-hidden="true"></span>
    </div>

    <p class="front__roles">Dietitian | Nutritionist | Chef</p>
  </section>

</main>
</body>
</html>
```